A start up Private Wine Label for export to Asia.

We are looking for the best graphic design for our very first wine label Corvessa Wines and would like the following requirements:

1. Black background - explore and play around the shade of black
2. Gold Shimmery Colour Font
3. Font should be a cursive classic posh that says Corvessa Wines
4. We would like the front graphic design to be simple and elegant and has a traditional classic feel to it.

Target Market(s)

Small scale to test the upper class market for export to Asia

Font styles to use
Script

Colors

Designer to choose colors to be used in the design.

Requirements
Must have
• Gold font for the label Corvessa Wines with shimmery touch to it.
• Elegant black background.
• Simple but elegant design.
• Attractive to the upper class market in Asia.
Nice to have
• Explore and play around with your imagination.

```html
<!DOCTYPE html>
<html lang="en">
<head>
<meta charset="utf-8">
<title>Corvessa Wines — Front Label</title>
<link rel="stylesheet" href="https://fonts.googleapis.com/css2?family=Great+Vibes&family=Mulish:ital,wght@1,400&display=swap">
<style>
  :root {
    --canvas: #ffffff;
    --label-black: #201f21;
    --label-black-soft: #2a292b;
    --gold-deep: #9a6b26;
    --gold-mid: #c99a4a;
    --gold-light: #f2d983;
    --gold-pale: #fbeaa6;
    --frame-gold: linear-gradient(90deg, var(--gold-deep) 0%, var(--gold-mid) 12%, var(--gold-light) 30%, var(--gold-mid) 45%, var(--gold-deep) 58%, var(--gold-light) 75%, var(--gold-mid) 88%, var(--gold-deep) 100%);
    --text-gold: linear-gradient(100deg, var(--gold-deep) 0%, var(--gold-light) 25%, var(--gold-mid) 45%, var(--gold-pale) 62%, var(--gold-deep) 82%, var(--gold-mid) 100%);
  }
  * { box-sizing: border-box; margin: 0; padding: 0; }
  html, body {
    width: 1200px;
    height: 1200px;
    overflow: hidden;
    background: var(--canvas);
  }
  .wine-label {
    position: absolute;
    left: 207px;
    top: 50px;
    width: 786px;
    height: 1100px;
    background: var(--frame-gold);
    padding: 31px;
  }
  .label-panel {
    position: relative;
    width: 100%;
    height: 100%;
    background: var(--label-black);
    overflow: hidden;
  }
  .bokeh-field {
    position: absolute;
    inset: 0;
    background:
      radial-gradient(ellipse at 30% 25%, rgba(255,255,255,0.035), transparent 55%),
      radial-gradient(ellipse at 70% 75%, rgba(255,255,255,0.04), transparent 60%),
      var(--label-black);
  }
  .gold-text {
    background: var(--text-gold);
    -webkit-background-clip: text;
    background-clip: text;
    color: transparent;
  }
  .brand-name {
    position: absolute;
    left: 0;
    right: 0;
    text-align: center;
    font-family: "Great Vibes", cursive;
    font-weight: 400;
    line-height: 1;
  }
  .brand-name--primary {
    top: 350px;
    font-size: 170px;
    padding: 0 20px;
  }
  .brand-name--secondary {
    top: 545px;
    font-size: 140px;
    padding-left: 20px;
  }
  .volume-note {
    position: absolute;
    left: 0;
    right: 0;
    top: 968px;
    text-align: center;
    font-family: "Mulish", sans-serif;
    font-style: italic;
    font-weight: 400;
    font-size: 34px;
    letter-spacing: 0.5px;
  }
</style>
</head>
<body>
  <main class="wine-label">
    <section class="label-panel">
      <div class="bokeh-field" role="img" aria-label="Faint dark bokeh dots scattered across the black label background"></div>
      <h1 class="brand-name brand-name--primary gold-text">Corvessa</h1>
      <p class="brand-name brand-name--secondary gold-text">Wines</p>
      <p class="volume-note gold-text">750 ml / ALC. 11% VOL</p>
    </section>
  </main>
</body>
</html>
```